Local Flower Farm Needs Business Card Design

I need business cards designed for a flower farm based in Eudora, Kansas.
Business Info:
We are a local cut flower farm located in Eudora, Kansas, founded by Corinne Haldwick. What started as a passion for agriculture and search for more joy in daily life has blossomed into a small business dedicated to providing the community with beautiful, fresh, and sustainable flowers. We specialize in local, seasonal blooms, ensuring that every petal reflects the care and dedication we pour into our craft. Our mission is to deliver the highest quality flowers directly to our customers through local farmers markets and to florists who share our commitment to sustainability. Join us in celebrating the beauty of nature, one bloom at a time!
Contact Details:
Corinne Haldwick
Owner
Phone 913-555-0147
Facebook: Rosalind Thorpe Gardens
Instagram: @RosalindThorpeGardens
Website: RosalindThorpeGardens.example
Target Market(s)
Wholesale to Florists and Direct to Consumer via Farmers Market
Industry/Entity Type
Florist, Farm
Contact Information for Business Card
Name, Contact Info, Logo
Look and feel
Each slider illustrates characteristics of the customer's brand and the style your logo design should communicate.

```html
<!DOCTYPE html>
<html lang="en">
<head>
<meta charset="utf-8">
<title>Rosalind Thorpe Gardens – Business Card</title>
<link href="https://fonts.googleapis.com/css2?family=Montserrat:wght@400;500;700&display=swap" rel="stylesheet">
<style>
  :root {
    --backdrop: #e6e6e8;
    --paper: #ffffff;
    --ink: #0a2a2e;
    --text: #1b1b1b;
    --faint: #e4e4e4;
    --teal-bright: #58c6e4;
    --teal-deep: #0b2a2e;
  }
  * { margin: 0; padding: 0; box-sizing: border-box; }
  html, body { width: 1200px; height: 1108px; overflow: hidden; background: var(--backdrop); font-family: "Montserrat", sans-serif; }
  .card { position: absolute; box-shadow: 0 14px 22px rgba(0,0,0,0.18); }
  .card-front { left: 219px; top: 50px; width: 775px; height: 473px; background: var(--paper); }
  .band { position: absolute; left: 0; top: 41px; width: 100%; height: 84px; background: var(--ink); }
  .brand-seal { position: absolute; left: 81px; top: 28px; width: 126px; height: 126px; border-radius: 50%; background: var(--paper); border: 2px solid var(--ink); display: flex; align-items: center; justify-content: center; text-align: center; }
  .brand-seal span { font-size: 13px; font-weight: 700; color: var(--ink); line-height: 1.3; width: 90px; }
  .holder { position: absolute; right: 51px; top: 52px; text-align: right; color: var(--paper); }
  .holder-name { font-size: 28px; font-weight: 700; letter-spacing: 0.2px; }
  .holder-role { font-size: 17px; font-weight: 400; margin-top: 2px; }
  .contacts { position: absolute; left: 40px; top: 334px; list-style: none; }
  .contacts li { display: flex; align-items: center; gap: 9px; font-size: 18px; color: var(--text); height: 28.5px; }
  .contacts svg { width: 17px; height: 17px; flex: none; }
  .faint-brand { position: absolute; left: 520px; top: 210px; width: 220px; font-size: 40px; font-weight: 700; line-height: 1.05; color: var(--faint); }
  .address { position: absolute; left: 535px; top: 401px; font-size: 18px; color: var(--text); line-height: 1.25; }
  .card-back { left: 217px; top: 568px; width: 777px; height: 456px; background: var(--teal-deep); overflow: hidden; }
  .pattern { position: absolute; inset: 0; background: linear-gradient(125deg, var(--teal-bright) 0%, #2f7f92 28%, #123d44 55%, var(--teal-deep) 78%); }
  .back-brand { position: absolute; left: 528px; top: 282px; width: 110px; font-size: 17px; font-weight: 700; line-height: 1.2; color: var(--paper); }
</style>
</head>
<body>
  <section class="card card-front">
    <div class="band"></div>
    <div class="brand-seal"><span>Rosalind Thorpe Gardens</span></div>
    <div class="holder">
      <div class="holder-name">Corinne Haldwick</div>
      <div class="holder-role">Owner</div>
    </div>
    <div class="faint-brand">Rosalind Thorpe Gardens</div>
    <ul class="contacts">
      <li><svg viewBox="0 0 24 24"><path d="M6.6 10.8a15 15 0 0 0 6.6 6.6l2.2-2.2a1 1 0 0 1 1-.25 11.4 11.4 0 0 0 3.6.6 1 1 0 0 1 1 1V20a1 1 0 0 1-1 1A17 17 0 0 1 3 4a1 1 0 0 1 1-1h3.5a1 1 0 0 1 1 1c0 1.25.2 2.45.6 3.6a1 1 0 0 1-.25 1z" fill="#1b1b1b"/></svg>913-555-0147</li>
      <li><svg viewBox="0 0 24 24"><circle cx="12" cy="12" r="10" fill="#1b1b1b"/></svg>Rosalind Thorpe Gardens</li>
      <li><svg viewBox="0 0 24 24"><circle cx="12" cy="12" r="10" fill="#1b1b1b"/></svg>@RosalindThorpeGardens</li>
      <li><svg viewBox="0 0 24 24" fill="none" stroke="#1b1b1b" stroke-width="2"><circle cx="12" cy="12" r="10"/><ellipse cx="12" cy="12" rx="4" ry="10"/><path d="M2 12h20"/></svg>www.RosalindThorpeGardens.example</li>
    </ul>
    <div class="address">418 Meadowlark Ln, #12<br>Eudora, KS 66025</div>
  </section>

  <section class="card card-back">
    <div class="pattern" role="img" aria-label="Repeating brand pattern fading from bright teal to deep teal"></div>
    <div class="back-brand">Rosalind Thorpe Gardens</div>
  </section>
</body>
</html>
```